Home Fund Guide

Have clients check their mortgage qualifications before they go looking for a mortgage lender. This program gains access to your lenders credit report / 3 scores without impacting your credit scores.

```html
<!DOCTYPE html>
<html lang="en">
<head>
<meta charset="utf-8">
<title>Home Fund Guide – Business Card</title>
<link rel="stylesheet" href="https://fonts.googleapis.com/css2?family=Open+Sans:wght@400;600;700&family=Roboto:wght@400;500;700&display=swap">
<style>
  :root {
    --backdrop: #2d2d30;
    --brand-blue: #1a4fc8;
    --brand-blue-deep: #1540a8;
    --brand-green: #1fc47a;
    --paper: #f4f4f2;
    --ink: #1d1d1f;
    --white: #ffffff;
  }
  * { box-sizing: border-box; margin: 0; padding: 0; }
  html, body { width: 1200px; height: 852px; overflow: hidden; }
  body {
    background: var(--backdrop);
    font-family: "Open Sans", Arial, sans-serif;
    position: relative;
  }
  .card {
    position: absolute;
    top: 276px;
    width: 520px;
    height: 300px;
    border-radius: 22px;
    overflow: hidden;
  }
  /* ---------- Front side ---------- */
  .card--front { left: 50px; background: var(--brand-blue); color: var(--white); }
  .card__band { position: absolute; inset: 0; width: 100%; height: 100%; }
  .front__brand {
    position: absolute; top: 26px; left: 0; right: 0;
    display: flex; align-items: center; justify-content: center; gap: 14px;
  }
  .brand-square {
    width: 34px; height: 34px; background: var(--white); border-radius: 4px;
  }
  .brand-name {
    font-family: "Open Sans", Arial, sans-serif;
    font-weight: 700; font-size: 38px; letter-spacing: -0.5px; line-height: 1;
    white-space: nowrap;
  }
  .front__tagline {
    position: absolute; top: 80px; left: 0; right: 0; text-align: center;
    font-size: 11.5px; font-weight: 400;
  }
  .front__benefits {
    position: absolute; top: 108px; left: 52px; right: 40px; list-style: none;
  }
  .front__benefits li {
    display: flex; align-items: flex-start; gap: 9px;
    font-size: 13px; font-weight: 600; line-height: 1.25;
    padding: 4px 0; border-bottom: 1px solid rgba(255,255,255,0.35);
  }
  .front__benefits li:last-child { border-bottom: none; }
  .tick { flex: 0 0 14px; width: 14px; height: 14px; margin-top: 1px; }
  .front__url {
    position: absolute; bottom: 26px; left: 0; right: 0;
    display: flex; align-items: center; justify-content: center; gap: 14px;
    font-size: 12.5px; font-weight: 600;
  }
  .front__url::before, .front__url::after {
    content: ""; width: 70px; height: 2px; background: var(--brand-green);
  }
  /* ---------- Back side ---------- */
  .card--back { left: 630px; background: var(--paper); color: var(--ink); }
  .back__wave { position: absolute; inset: 0; width: 100%; height: 100%; }
  .back__brand {
    position: absolute; left: 24px; top: 92px; width: 230px;
    display: flex; flex-direction: column; align-items: center; gap: 12px;
  }
  .back__brand .brand-square { width: 60px; height: 60px; background: var(--brand-blue); border-radius: 6px; }
  .back__brand .brand-name { font-size: 25px; color: var(--brand-blue); }
  .back__person { position: absolute; top: 22px; right: 32px; text-align: right; font-family: "Roboto", Arial, sans-serif; }
  .person__name { font-size: 22px; font-weight: 700; color: var(--brand-blue); line-height: 1.2; }
  .person__name .surname { color: var(--brand-green); }
  .person__role { font-size: 12.5px; font-weight: 500; margin-top: 2px; }
  .back__address {
    position: absolute; top: 84px; right: 32px; text-align: right;
    font-family: "Roboto", Arial, sans-serif; font-size: 12.5px; line-height: 1.4;
  }
  .back__contact {
    position: absolute; bottom: 22px; right: 26px; list-style: none;
    font-family: "Roboto", Arial, sans-serif; font-size: 13px; color: var(--white);
    text-align: right; line-height: 1.5;
  }
  .back__contact li { display: flex; align-items: center; justify-content: flex-end; gap: 6px; }
  .contact-icon { width: 12px; height: 12px; }
</style>
</head>
<body>

<section class="card card--front" aria-label="Business card front">
  <svg class="card__band" viewBox="0 0 520 300" preserveAspectRatio="none" aria-hidden="true">
    <polygon points="0,70 520,58 520,210 0,232" fill="var(--brand-green)"/>
  </svg>
  <div class="front__brand">
    <span class="brand-square"></span>
    <span class="brand-name">Home Fund Guide</span>
  </div>
  <p class="front__tagline">is Managed by Harbor Lane Financial, A 401(c)(3) Nonprofit Certified Credit Counselor</p>
  <ul class="front__benefits">
    <li><svg class="tick" viewBox="0 0 14 14"><rect width="14" height="14" rx="2" fill="#fff"/><path d="M3 7.5l2.5 2.5L11 4" stroke="var(--brand-blue)" stroke-width="2" fill="none"/></svg>Discover Your Mortgage Qualifications - FHA, Conv., VA, USDA</li>
    <li><svg class="tick" viewBox="0 0 14 14"><rect width="14" height="14" rx="2" fill="#fff"/><path d="M3 7.5l2.5 2.5L11 4" stroke="var(--brand-blue)" stroke-width="2" fill="none"/></svg>Find Out Your Lender's 3 ScoreLine (Classic) Scores</li>
    <li><svg class="tick" viewBox="0 0 14 14"><rect width="14" height="14" rx="2" fill="#fff"/><path d="M3 7.5l2.5 2.5L11 4" stroke="var(--brand-blue)" stroke-width="2" fill="none"/></svg>Your Credit Report will be Analyzed for Score Improvement</li>
    <li><svg class="tick" viewBox="0 0 14 14"><rect width="14" height="14" rx="2" fill="#fff"/><path d="M3 7.5l2.5 2.5L11 4" stroke="var(--brand-blue)" stroke-width="2" fill="none"/></svg>HFG will Identify Your Personal Steps to Higher ScoreLine Scores<br>(66 Average Point Improvement)</li>
  </ul>
  <p class="front__url">www.HomeFundGuide.org</p>
</section>

<section class="card card--back" aria-label="Business card back">
  <svg class="back__wave" viewBox="0 0 520 300" preserveAspectRatio="none" aria-hidden="true">
    <path d="M520,160 C430,162 330,190 290,240 C260,275 200,288 0,292 L0,300 L520,300 Z" fill="var(--brand-blue)"/>
    <path d="M520,148 C426,150 322,178 280,230 C250,266 190,278 0,281" stroke="var(--brand-green)" stroke-width="7" fill="none"/>
    <path d="M520,136 C420,138 312,166 268,220 C238,256 180,268 0,270" stroke="var(--brand-green)" stroke-width="3" fill="none"/>
  </svg>
  <div class="back__brand">
    <span class="brand-square"></span>
    <span class="brand-name">Home Fund Guide</span>
  </div>
  <div class="back__person">
    <p class="person__name">Dana <span class="surname">Reyes</span></p>
    <p class="person__role">Managing Director</p>
  </div>
  <p class="back__address">518 Mill Road, Suite 210,<br>Cedar Hollow, Wyoming 82070</p>
  <ul class="back__contact">
    <li>(877) 555-0142 <svg class="contact-icon" viewBox="0 0 12 12"><path d="M2 1h2.5l1 3-1.5 1a6 6 0 0 0 3 3l1-1.5 3 1V10a1 1 0 0 1-1 1C5 11 1 7 1 2a1 1 0 0 1 1-1z" fill="#fff"/></svg></li>
    <li>www.HomeFundGuide.org <svg class="contact-icon" viewBox="0 0 12 12"><rect x="1" y="2.5" width="10" height="7" fill="#fff"/><path d="M1 2.5l5 4 5-4" stroke="var(--brand-blue)" fill="none"/></svg></li>
    <li>Support@HomeFundGuide.org <svg class="contact-icon" viewBox="0 0 12 12"><circle cx="6" cy="6" r="5" fill="#fff"/><path d="M1 6h10M6 1c-2 2.5-2 7.5 0 10M6 1c2 2.5 2 7.5 0 10" stroke="var(--brand-blue)" stroke-width="0.8" fill="none"/></svg></li>
  </ul>
</section>

</body>
</html>
```